Mira Bloom Fitness Coaching Project

I am a personal trainer based in London. My services include one-on-one PT sessions, bootcamps.
I would like the design to be minimalistic. With light colours: white, pink, purple.
I specialise in weight loss, flexibility, mobility.

Tessa Brogan
Personal Trainer
Email: tessa.brogan@quellmail.com
tel: 07700218493
Instagram: Mira Bloom

Target Market(s)

adults, mostly females (age 18-50).

Industry/Entity Type

Fitness

Contact Information for Business Card

Tessa Brogan
Personal Trainer
tel: 07700218493
Instagram: Mira Bloom

Font styles to use
Serif

Colors
eea4c8
fbd4d5
fdf9cf
cfeae6
cee9f5

Requirements
Nice to have
• minimalistic style
• easy to read and remember

```html
<!DOCTYPE html>
<html lang="en">
<head>
<meta charset="utf-8">
<title>Tessa Brogan – Personal Trainer Business Card</title>
<link href="https://fonts.googleapis.com/css2?family=Open+Sans:wght@400;700&display=swap" rel="stylesheet">
<style>
  :root {
    --backdrop: #e4e4e6;
    --card: #ffffff;
    --card-shade: #f3f3f4;
    --accent-pink: #ec4fc9;
    --text-grey: #5f5f62;
    --photo-dark: #3a2a1e;
    --photo-mid: #8a5a38;
    --photo-light: #d9b48e;
    --photo-blossom: #c8443f;
  }
  * { margin: 0; padding: 0; box-sizing: border-box; }
  html, body {
    width: 1200px;
    height: 900px;
    overflow: hidden;
    background: var(--backdrop);
    font-family: "Open Sans", Arial, sans-serif;
  }
  .business-card {
    position: absolute;
    left: 150px;
    top: 193px;
    width: 900px;
    height: 514px;
    background: linear-gradient(120deg, var(--card) 0%, var(--card-shade) 100%);
    overflow: hidden;
    box-shadow: 0 10px 30px rgba(0,0,0,0.18);
  }
  .portrait-area {
    position: absolute;
    right: 0;
    top: 0;
    width: 540px;
    height: 100%;
    background:
      radial-gradient(ellipse 40% 30% at 85% 80%, var(--photo-blossom) 0%, transparent 70%),
      radial-gradient(ellipse 45% 55% at 55% 45%, var(--photo-light) 0%, var(--photo-mid) 55%, var(--photo-dark) 100%);
    -webkit-mask-image: linear-gradient(90deg, transparent 0%, rgba(0,0,0,0.35) 22%, #000 48%);
    mask-image: linear-gradient(90deg, transparent 0%, rgba(0,0,0,0.35) 22%, #000 48%);
  }
  .accent-tab {
    position: absolute;
    left: 0;
    top: 274px;
    width: 10px;
    height: 64px;
    background: var(--accent-pink);
    border-radius: 0 4px 4px 0;
  }
  .identity {
    position: absolute;
    left: 48px;
    top: 270px;
  }
  .identity .name {
    color: var(--accent-pink);
    font-weight: 700;
    font-size: 27px;
    line-height: 1.1;
    letter-spacing: 0.3px;
    text-transform: uppercase;
  }
  .identity .role {
    color: var(--text-grey);
    font-size: 26px;
    line-height: 1.2;
    text-transform: uppercase;
  }
  .contact-list {
    position: absolute;
    left: 48px;
    top: 352px;
    list-style: none;
    color: var(--text-grey);
    font-size: 23px;
    line-height: 30px;
  }
  .contact-list li {
    display: flex;
    align-items: center;
    gap: 14px;
  }
  .contact-list .icon {
    width: 20px;
    height: 20px;
    flex: none;
  }
  .contact-list .social-mark {
    width: 18px;
    height: 18px;
    background: var(--accent-pink);
    flex: none;
    margin: 0 1px;
  }
  .contact-list .services {
    padding-top: 4px;
  }
</style>
</head>
<body>
  <div class="business-card">
    <div class="portrait-area" role="img" aria-label="Photo of the smiling personal trainer with long curly hair, outdoors in warm sunlight"></div>
    <div class="accent-tab"></div>
    <div class="identity">
      <p class="name">Tessa Brogan</p>
      <p class="role">Personal Trainer</p>
    </div>
    <ul class="contact-list">
      <li>
        <svg class="icon" viewBox="0 0 20 20" aria-hidden="true">
          <path d="M3 7c0-2 3-4 7-4s7 2 7 4v1.5h-4V7H7v1.5H3z" fill="#ec4fc9"/>
          <rect x="4" y="10" width="12" height="7" rx="1.5" fill="#ec4fc9"/>
          <circle cx="10" cy="13.5" r="2" fill="#fff"/>
        </svg>
        <span>07700218493</span>
      </li>
      <li>
        <svg class="icon" viewBox="0 0 20 20" aria-hidden="true">
          <rect x="2" y="5" width="16" height="11" rx="1.5" fill="#ec4fc9"/>
          <path d="M2.5 6l7.5 5.5L17.5 6" stroke="#fff" stroke-width="1.4" fill="none"/>
        </svg>
        <span>tessa.brogan@quellmail.com</span>
      </li>
      <li>
        <span class="social-mark" aria-hidden="true"></span>
        <span>Mira Bloom</span>
      </li>
      <li class="services">PT sessions, bootcamps.</li>
    </ul>
  </div>
</body>
</html>
```